Local fast-growing company in the service sector

We are looking for a modern business card design, which should also appear on our letterheads

Target Market(s)

Private and industrial sectors

Contact Information for Business Card

Vorname Name
Kellberger Str. 18
71288 Lindental
Tel.: 07146-839214-0
Name@agentur-kvtl.de

Colors
9d9d9d
919191
aaaaaa

Requirements
Must have
• The logo (file) in silver

```html
<!DOCTYPE html>
<html lang="de">
<head>
<meta charset="utf-8">
<title>KVTL Visitenkarte</title>
<link href="https://fonts.googleapis.com/css2?family=Open+Sans:wght@400;600;700&display=swap" rel="stylesheet">
<style>
  :root {
    --page-bg: #e9e7e4;
    --card-dark: #474545;
    --panel-light: #d4d4d6;
    --panel-lighter: #dcdcde;
    --silver: #aaaaaa;
    --text-light: #f4f4f4;
    --text-dark: #2b2b2b;
  }
  html, body {
    margin: 0;
    width: 1200px;
    height: 900px;
    overflow: hidden;
    background: var(--page-bg);
    font-family: "Open Sans", Arial, sans-serif;
  }
  .business-card {
    position: absolute;
    left: 112px;
    top: 150px;
    width: 975px;
    height: 600px;
    background: var(--card-dark);
    overflow: hidden;
    box-shadow: 0 12px 30px rgba(0,0,0,0.18);
  }
  .card-panel {
    position: absolute;
    inset: 0;
    width: 100%;
    height: 100%;
  }
  .brand-name {
    position: absolute;
    left: 52px;
    top: 110px;
    margin: 0;
    font-size: 96px;
    font-weight: 700;
    letter-spacing: 4px;
    line-height: 1;
    color: var(--silver);
  }
  .person-name {
    position: absolute;
    left: 60px;
    top: 385px;
    margin: 0;
    font-size: 33px;
    font-weight: 400;
    color: var(--text-light);
  }
  .contact-list {
    position: absolute;
    left: 55px;
    top: 448px;
    margin: 0;
    padding: 0;
    list-style: none;
    color: var(--text-light);
    font-size: 25px;
  }
  .contact-list li {
    display: flex;
    align-items: center;
    height: 36px;
  }
  .contact-list svg {
    width: 22px;
    height: 22px;
    margin-right: 10px;
    fill: var(--text-light);
  }
  .address {
    position: absolute;
    right: 50px;
    top: 478px;
    margin: 0;
    font-style: normal;
    text-align: right;
    font-size: 25px;
    line-height: 37px;
    color: var(--text-dark);
  }
</style>
</head>
<body>
  <div class="business-card">
    <svg class="card-panel" viewBox="0 0 650 400" preserveAspectRatio="none" aria-hidden="true">
      <path d="M507 0 H650 V400 H312 L420 270 V108 Q420 95 432 88 Z" fill="var(--panel-light)"/>
      <path d="M575 0 H650 V380 H467 V95 Z" fill="var(--panel-lighter)"/>
    </svg>

    <p class="brand-name">KVTL</p>

    <p class="person-name">VORNAME NAME</p>
    <ul class="contact-list">
      <li>
        <svg viewBox="0 0 24 24"><path d="M6.6 10.8a15 15 0 0 0 6.6 6.6l2.2-2.2c.3-.3.7-.4 1-.2 1.1.4 2.3.6 3.6.6.6 0 1 .4 1 1V20c0 .6-.4 1-1 1A17 17 0 0 1 3 4c0-.6.4-1 1-1h3.5c.6 0 1 .4 1 1 0 1.3.2 2.5.6 3.6.1.3 0 .7-.2 1z"/></svg>
        07146-839214-0
      </li>
      <li>
        <svg viewBox="0 0 24 24"><path d="M2 5h20v14H2z M3.5 6.5 12 13l8.5-6.5" fill="none" stroke="var(--text-light)" stroke-width="2"/></svg>
        Name@agentur-kvtl.de
      </li>
      <li>
        <svg viewBox="0 0 24 24"><circle cx="12" cy="12" r="10"/><path d="M7 8c2 0 3 1 3 3s-2 2-2 4M14 4c0 2 2 2 3 3s0 3 2 4" fill="none" stroke="var(--card-dark)" stroke-width="1.6"/></svg>
        www.agentur-kvtl.de
      </li>
    </ul>

    <address class="address">
      Kellberger Str. 18<br>
      71288 Lindental
    </address>
  </div>
</body>
</html>
```